Design for a 4 screens iOS and Android app - "VelaTrakko"

The app allows you to track your car gasoline refill ...
We need a design for the 4 screens of the app:
a) 1 form with 3 fields.
b) 1 simple list view
c) 1 summary view
d) 1 text page
2 "alerts" items are also to be designed.
No specific guidelines, nor logo or whatever.
It will be a free app distributed on iOS and Androïd.
We just want to make it looking nice & very usable for end users.
Target Market(s)
B2C app
Industry/Entity Type
Android

```html
<!DOCTYPE html>
<html lang="en">
<head>
<meta charset="utf-8">
<title>VelaTrakko – Refill history</title>
<link href="https://fonts.googleapis.com/css2?family=Roboto:wght@400;700;900&display=swap" rel="stylesheet">
<style>
  :root {
    --brand-blue: #0288f7;
    --row-tint: #d9effc;
    --surface: #ffffff;
    --divider: #ffffff;
  }
  * { box-sizing: border-box; margin: 0; padding: 0; }
  html, body { width: 675px; height: 1200px; overflow: hidden; background: var(--surface); }
  body { font-family: "Roboto", sans-serif; color: var(--brand-blue); }

  .app { width: 675px; height: 1200px; position: relative; overflow: hidden; background: var(--surface); }

  .toolbar { display: flex; height: 106px; background: var(--brand-blue); }
  .toolbar__button {
    flex: 1; display: flex; align-items: center; justify-content: center;
    border-right: 1px solid var(--divider);
  }
  .toolbar__button:last-child { border-right: none; }
  .toolbar__icon { display: block; }

  .refill-list { list-style: none; }
  .refill__date {
    height: 108px; display: flex; align-items: center; justify-content: center;
    font-weight: 900; font-size: 32px; letter-spacing: 0.3px; word-spacing: 10px;
    background: var(--surface);
  }
  .refill__data {
    height: 160px; background: var(--row-tint); position: relative;
    font-weight: 400; font-size: 32px;
  }
  .refill__value { position: absolute; top: 50%; transform: translateY(-50%); white-space: nowrap; }
  .refill__distance { left: 42px; top: 52%; }
  .refill__volume { left: 355px; transform: translate(-50%, -50%); top: 46%; }
  .refill__cost { right: 38px; top: 46%; }
</style>
</head>
<body>
<main class="app">
  <nav class="toolbar">
    <div class="toolbar__button" aria-label="Add refill">
      <svg class="toolbar__icon" width="46" height="46" viewBox="0 0 46 46">
        <path d="M23 1v44M1 23h44" stroke="#fff" stroke-width="4" stroke-linecap="round"/>
      </svg>
    </div>
    <div class="toolbar__button" aria-label="Refill list">
      <svg class="toolbar__icon" width="64" height="44" viewBox="0 0 64 44">
        <g fill="#fff">
          <circle cx="5" cy="4" r="4.5"/><circle cx="5" cy="22" r="4.5"/><circle cx="5" cy="40" r="4.5"/>
        </g>
        <g stroke="#fff" stroke-width="4" stroke-linecap="round">
          <path d="M18 4h44M18 22h44M18 40h44"/>
        </g>
      </svg>
    </div>
    <div class="toolbar__button" aria-label="Summary">
      <svg class="toolbar__icon" width="60" height="46" viewBox="0 0 60 46">
        <path d="M2 2v42h56" fill="none" stroke="#fff" stroke-width="4" stroke-linecap="round" stroke-linejoin="round"/>
        <path d="M9 38V24l8-8 8 9 10-12 16 25z" fill="#fff"/>
      </svg>
    </div>
  </nav>

  <ul class="refill-list">
    <li class="refill">
      <div class="refill__date">15 Feb. 2016 14:24</div>
      <div class="refill__data">
        <span class="refill__value refill__distance">127500 km</span>
        <span class="refill__value refill__volume">49,88 l</span>
        <span class="refill__value refill__cost">47,25€</span>
      </div>
    </li>
    <li class="refill">
      <div class="refill__date">08 Feb. 2016 13:14</div>
      <div class="refill__data">
        <span class="refill__value refill__distance">126500 km</span>
        <span class="refill__value refill__volume">50,11 l</span>
        <span class="refill__value refill__cost">49,75€</span>
      </div>
    </li>
    <li class="refill">
      <div class="refill__date">01 Feb. 2016 11:17</div>
      <div class="refill__data">
        <span class="refill__value refill__distance">125500 km</span>
        <span class="refill__value refill__volume">42,50 l</span>
        <span class="refill__value refill__cost">44,70€</span>
      </div>
    </li>
    <li class="refill">
      <div class="refill__date">27 Jan. 2016 12:21</div>
      <div class="refill__data">
        <span class="refill__value refill__distance">123500 km</span>
        <span class="refill__value refill__volume">49,88 l</span>
        <span class="refill__value refill__cost">47,25€</span>
      </div>
    </li>
  </ul>
</main>
</body>
</html>
```